Logo + Label Design (Men’s Grooming Brand & Product Packaging)

Design a logo and 2 oz pomade label for Brel, a modern men’s grooming brand focused on clean, high-quality, natural ingredients. The design should establish a bold, masculine, minimalist identity that can later extend to products like shaving gel and body wash.

Key Requirements

Create a primary logo for “Brel” and a core label for the 2 oz pomade jar (screw-top).

Use a clean, modern style — masculine, confident, and approachable (think Dorran’s, Velta, Northfield Kit).

Design for 1–2 color screen printing on solid jar colors (white, black, or navy).

Avoid gradients, foil, or embossing. Must work in black & white.

Provide: vector logo, mockup of the 2 oz jar, color palette (CMYK/RGB/HEX), and font specs.

Winning design may lead to future projects (body wash, shave gel, skincare lines).

Font styles to use
Other font styles liked:
• We like the fonts and design concept in the attached mockup.

Requirements
Should not have
• We want to avoid too much writing or busy designs. We want to avoid having graphics/illustrations embedded in the logo if they will cause the brand to look less classy or sophisticated. We also want the design to look simple and all-American (e.g. Hollister and Vane, Pine Ledger, The KIM, etc). We’d like to give a Pellham & Royce vibe that feels classy and high end.

```html
<!DOCTYPE html>
<html lang="en">
<head>
<meta charset="utf-8">
<title>Brel Hair Pomade – Jar Label and Lid</title>
<link rel="stylesheet" href="https://fonts.googleapis.com/css2?family=Libre+Bodoni:wght@400&family=Jost:wght@400;500;600&display=swap">
<style>
  :root {
    --backdrop: #adada2;
    --label-white: #ffffff;
    --ink: #111111;
    --ink-soft: #2e2e2e;
    --accent-blue: #1f6ea6;
  }
  * { margin: 0; padding: 0; box-sizing: border-box; }
  html, body { width: 1200px; height: 1200px; overflow: hidden; }
  body {
    background: var(--backdrop);
    position: relative;
    font-family: "Jost", "Helvetica Neue", Arial, sans-serif;
    color: var(--ink);
  }

  /* Wrap-around jar label */
  .wrap-label {
    position: absolute;
    left: 26px;
    top: 400px;
    width: 1148px;
    height: 137px;
    background: var(--label-white);
  }
  .directions {
    position: absolute;
    left: 12px;
    top: 22px;
    width: 378px;
    font-size: 12.6px;
    line-height: 15.5px;
    letter-spacing: 0.05em;
    color: var(--ink-soft);
    text-transform: uppercase;
  }
  .directions .line {
    display: block;
    text-align: justify;
    text-align-last: justify;
    white-space: nowrap;
  }
  .directions .line.last,
  .directions .line.heading { text-align-last: left; }
  .product-type {
    position: absolute;
    left: 440px;
    top: 68px;
    transform: translate(-50%, -50%) rotate(-90deg);
    font-size: 13.6px;
    font-weight: 500;
    letter-spacing: 0.06em;
    white-space: nowrap;
    color: var(--ink-soft);
  }
  .wordmark {
    position: absolute;
    left: 470px;
    top: 0;
    width: 320px;
    height: 137px;
    display: flex;
    align-items: center;
    justify-content: center;
    padding-top: 6px;
    font-family: "Libre Bodoni", "Bodoni Moda", Didot, serif;
    font-weight: 400;
    font-size: 108px;
    line-height: 1;
    color: var(--ink);
    letter-spacing: -0.01em;
    white-space: nowrap;
  }
  .variant {
    position: absolute;
    left: 807px;
    top: 6px;
  }
  .variant .scent {
    font-size: 21px;
    font-weight: 500;
    letter-spacing: 0.07em;
    color: var(--accent-blue);
    line-height: 26px;
  }
  .variant .spec {
    font-size: 14.5px;
    font-weight: 600;
    letter-spacing: 0.08em;
    color: var(--ink-soft);
    line-height: 24px;
  }
  .net-weight {
    position: absolute;
    left: 808px;
    top: 91px;
    width: 83px;
    border: 2px solid var(--ink-soft);
    font-size: 11px;
    font-weight: 600;
    text-align: center;
    color: var(--ink-soft);
    line-height: 16px;
  }
  .net-weight span { display: block; }
  .net-weight span + span { border-top: 2px solid var(--ink-soft); }
  .maker {
    position: absolute;
    left: 994px;
    top: 60px;
    font-size: 9.8px;
    font-weight: 500;
    line-height: 12.4px;
    color: var(--ink);
    text-transform: uppercase;
  }

  /* Lid top */
  .lid {
    position: absolute;
    left: 496px;
    top: 556px;
    width: 208px;
    height: 208px;
    border-radius: 50%;
    background: var(--label-white);
    text-align: center;
  }
  .lid .wordmark-small {
    margin-top: 50px;
    font-family: "Libre Bodoni", "Bodoni Moda", Didot, serif;
    font-size: 50px;
    line-height: 52px;
    color: var(--ink);
  }
  .lid .product-type-small {
    margin-top: 6px;
    font-size: 10.5px;
    font-weight: 400;
    letter-spacing: 0.08em;
    color: var(--ink-soft);
  }
  .lid .rule {
    width: 42px;
    height: 1px;
    background: var(--ink-soft);
    margin: 7px auto 8px;
  }
  .lid .scent-small {
    font-size: 6.5px;
    font-weight: 600;
    letter-spacing: 0.08em;
    color: var(--accent-blue);
  }
  .lid .spec-small {
    margin-top: 3px;
    font-size: 5.6px;
    line-height: 7.5px;
    letter-spacing: 0.06em;
    color: var(--ink-soft);
  }
</style>
</head>
<body>
  <section class="wrap-label">
    <p class="directions">
      <span class="line heading">Directions:</span>
      <span class="line">Melt small amount of pomade between hands</span>
      <span class="line">before massaging into damp hair (for sleeker</span>
      <span class="line">look) or dry hair (for more texture). Style as</span>
      <span class="line">desired. For external use only. Avoid contact</span>
      <span class="line last">with eyes. If irritation occurs, discontinue use.</span>
    </p>
    <p class="product-type">HAIR POMADE</p>
    <h1 class="wordmark">BREL</h1>
    <div class="variant">
      <p class="scent">FRESH &amp; CLEAN</p>
      <p class="spec">MEDIUM HOLD</p>
      <p class="spec" style="margin-top:1px">MATTE FINISH</p>
    </div>
    <p class="net-weight"><span>NET WT 2 OZ</span><span>(57 G)</span></p>
    <p class="maker">Manufactured by:<br>Brel Health Products,<br>Ashford, NC 27501<br>Visit us at<br>brelhealthproducts.com</p>
  </section>

  <section class="lid">
    <p class="wordmark-small">BREL</p>
    <p class="product-type-small">HAIR POMADE</p>
    <div class="rule"></div>
    <p class="scent-small">FRESH &amp; CLEAN</p>
    <p class="spec-small">MEDIUM HOLD<br>MATTE FINISH</p>
  </section>
</body>
</html>
```